20 year old business card needs re-design

We need to redesign our corporate business card look. We need something that appears more modern, eye catchy but professional.

Target Market(s)

manufacturing industry

Industry/Entity Type

Manufacturer

Contact Information for Business Card

One side can have the logo. Other side can have contact information.

Font styles to use
Serif

Colors
3277b5
33b8a4
ffffff

Requirements
Must have
• Eye catchy - need to standout from the crowd. company logo cannot change. Full name, job title, phone number and email address.
Should not have
• Fax, business address is not necessary.

```html
<!DOCTYPE html>
<html lang="en">
<head>
<meta charset="utf-8">
<title>Norvale Industrial – Business Card</title>
<link rel="stylesheet" href="https://fonts.googleapis.com/css2?family=Arimo:wght@400;700&family=Open+Sans:wght@700&display=swap">
<style>
  :root {
    --backdrop: #2a2a2a;
    --brand-blue: #1f56a8;
    --brand-blue-deep: #17479a;
    --card-white: #ffffff;
    --card-shade: #ecedef;
    --ink: #1c1c1c;
    --ink-soft: #2e2e2e;
  }
  * { box-sizing: border-box; margin: 0; padding: 0; }
  html, body {
    width: 1200px; height: 997px; overflow: hidden;
    background: var(--backdrop);
  }
  .stage {
    position: relative; width: 1200px; height: 997px;
  }
  .card {
    position: absolute;
    width: 520px; height: 297px;
    border-radius: 3px;
    overflow: hidden;
  }
  /* Logo side */
  .card--front {
    left: 60px; top: 200px;
    background: var(--brand-blue);
    display: flex; align-items: center; justify-content: center;
  }
  .wordmark {
    font-family: "Arimo", Arial, sans-serif;
    font-weight: 700;
    letter-spacing: -1px;
    line-height: 1;
  }
  .card--front .wordmark { color: var(--card-white); font-size: 58px; }

  /* Contact side */
  .card--back {
    left: 620px; top: 420px;
    background: linear-gradient(180deg, var(--card-white) 0%, var(--card-shade) 100%);
  }
  .card--back .wordmark {
    position: absolute; left: 0; right: 0; top: 46px;
    text-align: center;
    color: var(--brand-blue); font-size: 46px;
  }
  .contact {
    position: absolute; right: 44px; top: 118px;
    text-align: right;
    font-family: "Arimo", Arial, sans-serif;
    font-size: 12.5px; line-height: 20px;
    color: var(--ink);
  }
  .contact-tab {
    position: absolute; right: 0; top: 116px;
    width: 24px; height: 64px;
    background: var(--brand-blue);
    border-radius: 6px 0 0 6px;
    display: flex; flex-direction: column; align-items: center; justify-content: space-around;
    padding: 4px 0;
  }
  .contact-tab svg { width: 11px; height: 11px; fill: var(--card-white); }
  .holder {
    position: absolute; left: 0; top: 192px;
    padding-left: 22px;
    font-family: "Open Sans", Arial, sans-serif;
  }
  .holder::before {
    content: ""; position: absolute; left: 0; top: 0;
    width: 10px; height: 40px;
    background: var(--brand-blue);
    border-radius: 0 5px 5px 0;
  }
  .holder-name { font-size: 16px; color: var(--brand-blue-deep); letter-spacing: 0.3px; }
  .holder-role { font-size: 11px; color: var(--ink-soft); letter-spacing: 0.3px; }
  .web-band {
    position: absolute; left: 0; right: 0; top: 240px; height: 20px;
    background: var(--brand-blue);
    text-align: right; padding-right: 40px;
    font-family: "Arimo", Arial, sans-serif; font-weight: 700;
    font-size: 13px; line-height: 20px; letter-spacing: 0.6px;
    color: var(--card-white);
  }
  .base-band {
    position: absolute; left: 0; right: 0; top: 272px; bottom: 0;
    background: var(--brand-blue);
  }
</style>
</head>
<body>
<main class="stage">
  <section class="card card--front" aria-label="Card front">
    <span class="wordmark">Norvale Industrial</span>
  </section>

  <section class="card card--back" aria-label="Card back">
    <span class="wordmark">Norvale Industrial</span>

    <address class="contact" style="font-style:normal">
      <div>+61 412 555 019</div>
      <div>hello@norvale.com.au</div>
      <div>Riverside QLD 4000</div>
    </address>

    <div class="contact-tab" aria-hidden="true">
      <svg viewBox="0 0 24 24"><path d="M6.6 10.8c1.4 2.8 3.8 5.1 6.6 6.6l2.2-2.2c.3-.3.7-.4 1-.2 1.1.4 2.3.6 3.6.6.6 0 1 .4 1 1V20c0 .6-.4 1-1 1C10.6 21 3 13.4 3 4c0-.6.4-1 1-1h3.5c.6 0 1 .4 1 1 0 1.3.2 2.5.6 3.6.1.3 0 .7-.2 1z"/></svg>
      <svg viewBox="0 0 24 24"><path d="M2 5h20v14H2z M2 5l10 8 10-8" stroke="#1f56a8" stroke-width="1.5"/></svg>
      <svg viewBox="0 0 24 24"><path d="M12 2a7 7 0 0 0-7 7c0 5 7 13 7 13s7-8 7-13a7 7 0 0 0-7-7zm0 9.5A2.5 2.5 0 1 1 12 6.5a2.5 2.5 0 0 1 0 5z"/></svg>
    </div>

    <div class="holder">
      <div class="holder-name">CLARA BENSON</div>
      <div class="holder-role">FOUNDER &amp; CEO</div>
    </div>

    <div class="web-band">WWW.NORVALEINDUSTRIAL.COM</div>
    <div class="base-band"></div>
  </section>
</main>
</body>
</html>
```